Business Card for beauty technology startup

Design Glimora Business Card for a Beauty, based on the website identity and colors (https://www.glimora-example.com).
Glimora is a beauty tech startup that gathers helpful product info for beauty lovers and consumers (such as availability on stores, price range and product reviews) for makeup products. The card design must be young, colorful but clean, and very modern.

Target Market(s)

woman, 15-35

Industry/Entity Type

Cosmetics

Contact Information for Business Card

Full Name, address, phone

Font styles to use
Other font styles liked:
• Advent Pro

Colors
e34297
86cfc6
ffffff
5c5c5c
e8e8e8
e667a6
b2b2b2

Requirements
Must have
• One full colored side with a creative design and another with card info
• Use Color palette: #95C5C5 and/or #D38AA5
• Use fonts: Advent Pro
• Use website identity: https://www.glimora-example.com
Nice to have
• If needed extra font: Roboto

```html
<!DOCTYPE html>
<html lang="en">
<head>
<meta charset="utf-8">
<title>Glimora Business Card</title>
<link rel="stylesheet" href="https://fonts.googleapis.com/css2?family=Advent+Pro:wght@300;400&family=Barlow+Semi+Condensed:wght@400;600&display=swap">
<style>
  :root {
    --backdrop: #e6e6e6;
    --rose: #c97f99;
    --rose-deep: #bd7590;
    --rose-text: #c07b95;
    --teal: #7fc2c1;
    --teal-text: #6fb3b4;
    --paper: #f7f7f5;
    --ink: #2f2a2d;
    --white: #ffffff;
  }
  * { margin: 0; padding: 0; box-sizing: border-box; }
  html, body {
    width: 1200px; height: 576px; overflow: hidden;
    background: var(--backdrop);
  }
  .stage { position: relative; width: 1200px; height: 576px; }
  .card {
    position: absolute; top: 138px;
    width: 484px; height: 294px;
    border-radius: 14px; overflow: hidden;
  }
  .card--front {
    left: 82px;
    background: linear-gradient(180deg, var(--rose) 0%, var(--rose-deep) 100%);
  }
  .card--back { left: 602px; background: var(--paper); }

  .faint-ring {
    position: absolute; border-radius: 50%;
    border: 14px solid rgba(255,255,255,0.08);
  }
  .card--front .faint-ring { left: 166px; top: 94px; width: 160px; height: 160px; }
  .card--back .faint-ring {
    left: 290px; top: -20px; width: 220px; height: 220px;
    border-color: rgba(0,0,0,0.035);
  }

  .brand { position: absolute; display: flex; align-items: center; }
  .brand__dot {
    border-radius: 50%; border: 1.5px solid currentColor; flex: none;
  }
  .brand__name {
    font-family: "Advent Pro", sans-serif; font-weight: 300;
    text-transform: uppercase; letter-spacing: 0.12em; line-height: 1;
  }
  .card--front .brand { left: 105px; top: 120px; color: var(--ink); gap: 26px; }
  .card--front .brand__dot { width: 54px; height: 54px; }
  .card--front .brand__name { font-size: 46px; }

  .card--back .brand { left: 28px; top: 34px; color: var(--rose-text); gap: 26px; }
  .card--back .brand__dot { width: 58px; height: 58px; }
  .card--back .brand__name { font-size: 46px; }

  .waves { position: absolute; inset: 0; }

  .holder {
    position: absolute; left: 28px; top: 134px;
    font-family: "Barlow Semi Condensed", sans-serif;
  }
  .holder__name {
    color: var(--teal-text); font-weight: 600; font-size: 18px;
    letter-spacing: 0.03em; text-transform: uppercase;
  }
  .holder__address {
    margin-top: 12px; color: var(--rose-text);
    font-size: 13.5px; line-height: 17px;
  }
  .contact {
    position: absolute; right: 26px; top: 223px;
    list-style: none;
    font-family: "Barlow Semi Condensed", sans-serif;
    font-size: 12.5px; color: var(--white);
  }
  .contact__item {
    display: flex; align-items: center; justify-content: flex-end;
    gap: 8px; height: 16.5px;
  }
  .contact__icon { width: 11px; height: 11px; flex: none; }
</style>
</head>
<body>
<main class="stage">
  <section class="card card--front" aria-label="Card front">
    <div class="faint-ring"></div>
    <div class="brand">
      <span class="brand__dot"></span>
      <span class="brand__name">Glimora</span>
    </div>
  </section>

  <section class="card card--back" aria-label="Card back">
    <div class="faint-ring"></div>
    <svg class="waves" width="484" height="294" viewBox="0 0 484 294" aria-hidden="true">
      <path d="M0,252 C80,278 190,262 285,222 C365,188 425,170 484,164 L484,294 L0,294 Z" fill="var(--rose)"/>
      <path d="M44,230 C130,252 235,228 320,188 C385,158 440,146 484,142 L484,152 C438,157 388,170 325,203 C240,246 130,256 44,230 Z" fill="var(--teal)"/>
    </svg>
    <div class="brand">
      <span class="brand__dot"></span>
      <span class="brand__name">Glimora</span>
    </div>
    <div class="holder">
      <p class="holder__name">Ellie Moran</p>
      <p class="holder__address">48, Linden Row, Maple Town,<br>Country - 204917</p>
    </div>
    <ul class="contact">
      <li class="contact__item">00 555 014 782
        <svg class="contact__icon" viewBox="0 0 12 12" aria-hidden="true"><path d="M2.5 1 L4.5 1 L5.2 3.4 L4 4.4 C4.6 5.8 6 7.2 7.6 8 L8.6 6.8 L11 7.5 L11 9.5 C11 10.4 10.2 11 9.3 11 C5 10.6 1.4 7 1 2.7 C1 1.8 1.6 1 2.5 1 Z" fill="none" stroke="#fff" stroke-width="1.1"/></svg>
      </li>
      <li class="contact__item">www.glimora-example.com
        <svg class="contact__icon" viewBox="0 0 12 12" aria-hidden="true"><g fill="none" stroke="#fff" stroke-width="1.2" stroke-linecap="round"><path d="M5 7 L7 5"/><path d="M6.5 3 L7.6 1.9 A2 2 0 0 1 10.1 4.4 L9 5.5"/><path d="M5.5 9 L4.4 10.1 A2 2 0 0 1 1.9 7.6 L3 6.5"/></g></svg>
      </li>
      <li class="contact__item">yourname@glimora-example.com
        <svg class="contact__icon" viewBox="0 0 12 12" aria-hidden="true"><g fill="none" stroke="#fff" stroke-width="1.1"><rect x="1" y="2.5" width="10" height="7"/><path d="M1 2.5 L6 6.5 L11 2.5"/></g></svg>
      </li>
    </ul>
  </section>
</main>
</body>
</html>
```